New Innovative Counselling and psychotherapy Service needs Business Card design

Keep it simple and professional. On one side, just company name and logo (perhaps in all blue) and maybe a tag line.

On other side (all white) my name and Qualifications in centre

Industry/Entity Type

Health And Wellness

Contact Information for Business Card

Dara Whelby
Counsellor & Psychotherapist
BSc (Psychol.), BA, Dip. (Couns. & Psych.), PG.Cert (CBT), FGTrK, ONRE

I will also require Mobile no, Email and web site address of which I'll pass on to final designer.

Font styles to use
Sans Serif

Requirements
Must have
• My Logo Only and please use the colours in logo that is in it.
Should not have
• Any other images

```html
<!DOCTYPE html>
<html lang="en">
<head>
<meta charset="utf-8">
<title>Brightlane Business Card</title>
<link href="https://fonts.googleapis.com/css2?family=Work+Sans:wght@300;400;600&display=swap" rel="stylesheet">
<style>
  :root{
    --stage:#1c1c1c;
    --charcoal:#2c2c2d;
    --paper:#ffffff;
    --blue:#45a3d8;
    --green:#8cc152;
    --ink:#3a3a3a;
  }
  *{margin:0;padding:0;box-sizing:border-box}
  html,body{width:1200px;height:963px;overflow:hidden;background:var(--stage);font-family:"Work Sans",Arial,sans-serif}
  .canvas{position:relative;width:1200px;height:963px}
  .card{position:absolute;left:240px;width:720px;height:410px;border-radius:14px;overflow:hidden}
  .card-front{top:50px;background:var(--paper)}
  .card-back{top:503px;background:var(--charcoal)}
  .swoosh{position:absolute;inset:0}
  .brand{position:absolute;left:40px;top:56px;display:flex;align-items:center;gap:12px;font-weight:300;font-size:32px;color:var(--ink)}
  .brand-dot{width:22px;height:22px;border-radius:50%;background:var(--blue)}
  .person{position:absolute;right:44px;top:228px;text-align:right;color:var(--ink)}
  .person-name{font-weight:600;font-size:32px;color:var(--blue);letter-spacing:.5px;text-transform:uppercase;line-height:1.1}
  .person-role{font-size:17px;margin-top:4px}
  .person-quals{font-size:15px;line-height:1.35;margin-top:4px}
  .divider{position:absolute;left:40px;right:44px;top:334px;height:1.5px;background:var(--green)}
  .contact{position:absolute;left:40px;top:346px;list-style:none;font-size:14px;color:var(--ink);line-height:20px}
  .contact li{display:flex;align-items:center;gap:8px}
  .contact svg{width:12px;height:12px;fill:none;stroke:var(--blue);stroke-width:2}
  .web-accent{color:var(--blue)}
  .back-brand{position:absolute;left:0;right:0;top:150px;display:flex;justify-content:center;align-items:center;gap:16px;font-weight:300;font-size:56px;color:var(--blue)}
  .back-brand .brand-dot{width:34px;height:34px}
  .back-web{position:absolute;left:0;right:0;top:268px;text-align:center;font-size:20px;color:#d8d8d8;letter-spacing:.5px}
  .back-web .web-accent{color:var(--green)}
</style>
</head>
<body>
<main class="canvas">
  <section class="card card-front" aria-label="Card front">
    <svg class="swoosh" viewBox="0 0 720 410" aria-hidden="true">
      <path d="M60 0 C260 30 360 50 430 110 C490 160 600 178 720 180 L720 0 Z" fill="var(--charcoal)"/>
      <path d="M30 22 C250 50 350 76 424 136 C486 188 600 204 720 207" fill="none" stroke="var(--green)" stroke-width="10"/>
      <path d="M40 6 C255 38 356 62 428 122 C488 173 600 190 720 193" fill="none" stroke="var(--blue)" stroke-width="14"/>
    </svg>
    <div class="brand"><span class="brand-dot"></span>Brightlane</div>
    <div class="person">
      <div class="person-name">Dara Whelby</div>
      <div class="person-role">Counsellor &amp; Psychotherapist</div>
      <div class="person-quals">BSc (Psychol.), BA, Dip. (Couns. &amp; Psych.), PG.Cert<br>(CBT), FGTrK, ONRE</div>
    </div>
    <div class="divider"></div>
    <ul class="contact">
      <li><svg viewBox="0 0 12 12"><path d="M3 1 L5 3.5 L4 5 Q5.5 7.5 7 8 L8.5 7 L11 9 L9.5 11 Q3 10 1 2.5 Z"/></svg><span>555-014-2270</span></li>
      <li><svg viewBox="0 0 12 12"><rect x="1" y="2.5" width="10" height="7"/><path d="M1 2.5 L6 6.5 L11 2.5"/></svg><span>info@brightlanecare.com</span></li>
      <li><svg viewBox="0 0 12 12"><circle cx="6" cy="6" r="5"/><path d="M1 6 H11 M6 1 Q3 6 6 11 Q9 6 6 1"/></svg><span>www.<span class="web-accent">brightlanecare</span>.com</span></li>
    </ul>
  </section>

  <section class="card card-back" aria-label="Card back">
    <div class="back-brand"><span class="brand-dot"></span>Brightlane</div>
    <div class="back-web">www.<span class="web-accent">brightlanecare</span>.com</div>
  </section>
</main>
</body>
</html>
```